Web design for facial expression recognition service

We offer a service which allows customers to film large panels of participants looking at some video/screen (e.g. an advertisement) and to analyze the facial expressions shown by the participants. We are looking for the design of a new website which will make it easy for our customers to setup and view the results of these experiments online.
Competitor's websites that may serve as a reference are:
http://www.moriventa.com/quelbo/#pane_overview
http://www.dunvarpix.com/homepage.aspx
https://www.tamlora.com/
The website will (for as far as the design is concerned) consist of three parts:
- A public home page (and perhaps some contact/news/about page), designed to catch the attention/interest potential customers.
- A (protected) project result page, showing the results in an interactive page with charts and numerical data.
- Pages (also protected) with fields and tables (setting up the project details).
The winner of this design project should provide us with at least one design for each of the above in order to get a complete 'theme' going which our developers can use. However, you are welcome to initially only provide the design for the project result page and/or home page.
We are looking for a modern, fresh, yet professional look (my client is a more established party in the field).
The final delivery should consist of layered Photoshop or Illustrator files.
Thank you in advance for participating!
Updates
Dear designers,
Project Deadline Extended
Reason: Extending the deadline by a few days to give designers a chance to submit designs for the other pages and process further feedback.
Target Market(s)
marketing research agencies (B2B service)
Requirements
Must have
- Home page:
- Basic advertisement of the service; some quick explanation of how it works
- A way to login for existing users
- A link/button/banner inviting people to sign up
- Navigation controls to 2-3 other pages
- Social media links (Facebook, LinkedIn group)
- Company logo (sorry, can't provide it as my client wishes to remain anonymous for now, but it's rounded and has blue as it's main color).
- Copyright / creator details
Project result page:
(see attachment 1 for a functional mockup - the design may follow this layout closely, or be completely different)
- Title
- A video player and basic numerical data
- Different views of the analysis results can dynamically be added/removed/collapsed/expanded; each one of these views will show some kind of chart, filters (combos), numerical data and a download button/link.
- A way to sign out, go to the main project page and go to the main page
- Logo
- Copyright
The form pages:
(see attachment 2 for a functional mockup of one of the pages; feel free to change some elements to better show the overall style)
- Title
- Text fields, combos, calendar pickers, tables, navigation links
- Logo
- Copyright
Nice to have
- Any creative text elements or product logo/symbol are a bonus. However, the basic "Lorem Ipsum" would do too.

```html
<!DOCTYPE html>
<html lang="en">
<head>
<meta charset="utf-8">
<title>Veldenmoor – Facial Expression Analysis</title>
<link href="https://fonts.googleapis.com/css2?family=Arimo:wght@400;700&family=Ubuntu:wght@400;500&family=Varela+Round&display=swap" rel="stylesheet">
<style>
:root{
  --blue-dark:#2a55a5;
  --blue-nav:#3b8de6;
  --blue-nav-light:#56a4ef;
  --blue-title:#1d84c8;
  --blue-head:#2a5aa8;
  --green:#3fa41b;
  --green-light:#9fe03b;
  --green-dark:#5aa816;
  --hero-bg:#e9e9e9;
  --band-bg:#f4f4f4;
  --box-bg:#f1f1f1;
  --text:#222;
  --muted:#555;
  --footer-bg:#505050;
  --footer-text:#cfcfcf;
  --white:#fff;
}
*{box-sizing:border-box;margin:0;padding:0}
html,body{width:1200px;height:1147px;overflow:hidden;background:var(--white)}
body{font-family:"Arimo",Arial,sans-serif;color:var(--text);position:relative}
.page{position:relative;width:1200px;height:1147px;overflow:hidden}
.abs{position:absolute}

/* header */
.topbar{left:0;top:0;width:1200px;height:35px;background:var(--blue-dark)}
.navband{left:0;top:35px;width:1200px;height:54px;background:linear-gradient(var(--blue-nav-light),var(--blue-nav))}
.brand{left:180px;top:20px;display:flex;align-items:center;gap:10px;color:var(--white);font-family:"Varela Round",sans-serif;font-size:28px}
.brand-dot{width:34px;height:34px;border-radius:50%;background:#41a6e0;border:3px solid var(--white)}
.search{left:837px;top:5px;width:184px;height:24px;border-radius:6px;background:var(--white);border:2px solid #c9d6e8;font-size:10px;color:#888;padding:4px 12px;display:flex;justify-content:space-between;align-items:center}
.main-nav{right:189px;top:52px;display:flex;align-items:center;font-family:"Ubuntu",sans-serif;font-weight:500;font-size:15px;color:var(--white)}
.main-nav a{color:inherit;text-decoration:none;padding:0 21px}
.main-nav a+a{border-left:1px solid rgba(255,255,255,.55)}
.main-nav a:last-child{padding-right:0}

/* hero */
.hero{left:0;top:89px;width:1200px;height:310px;background:var(--hero-bg)}
.hero-media{left:182px;top:117px;width:518px;height:299px;border-radius:10px 10px 4px 4px;background:linear-gradient(#1a1a1a 0 3%,#b9d4ec 3% 88%,#1a1a1a 88% 93%,#d8d8d8 93%)}
.play{left:420px;top:240px;width:50px;height:34px;border-radius:6px;background:rgba(255,255,255,.85)}
.hero-title{left:698px;top:133px;width:330px;font-family:"Varela Round",sans-serif;font-weight:400;font-size:15px;line-height:22px;color:var(--blue-head);white-space:nowrap}
.hero-text{left:698px;top:191px;width:319px;font-size:10.3px;line-height:18.6px;text-align:justify}
.signup{left:697px;top:282px;width:228px;height:61px;border-radius:6px;background:linear-gradient(var(--green-light),var(--green-dark));border:1px solid #6cb31f;display:flex;align-items:center;justify-content:space-between;padding:0 18px 0 26px;color:var(--white);font-family:"Ubuntu",sans-serif;font-size:21px;letter-spacing:.5px;text-decoration:none}
.signup-arrow{width:28px;height:28px;border-radius:50%;background:#3f7d0f;display:flex;align-items:center;justify-content:center}
.dots{left:790px;top:357px;display:flex;gap:1px}
.dots span{width:8px;height:8px;border-radius:50%;background:#b9b9b9}
.dots span:first-child{background:#2b8fd6}

/* about */
.section-title{font-family:"Varela Round",sans-serif;font-weight:400;font-size:20px;color:var(--blue-title)}
.about-title{left:187px;top:456px}
.about-lead{left:187px;top:492px;width:548px;font-weight:700;font-size:10.3px;line-height:18.6px;letter-spacing:-.05px}
.about-text{left:187px;top:536px;width:538px;font-size:10.3px;line-height:18.6px;text-align:justify}

.login{left:755px;top:459px;width:262px;height:192px;border-radius:9px;background:var(--box-bg)}
.login-title{left:19px;top:14px;font-family:"Varela Round",sans-serif;font-size:15px;color:var(--blue-title)}
.field{left:15px;width:211px;height:22px;border-radius:11px;border:1px solid #ddd;background:var(--white);font-family:"Varela Round",sans-serif;font-size:10px;padding:0 15px;color:#999}
.field::placeholder{color:#c3c3c3}
.login-btn{left:28px;top:111px;width:68px;height:24px;border-radius:8px;background:linear-gradient(#4fa6f0,#1a6fd6);color:var(--white);font-family:"Ubuntu",sans-serif;font-size:13px;display:flex;align-items:center;justify-content:center}
.login-small{font-size:10px;color:var(--muted)}
.remember{left:28px;top:147px;display:flex;align-items:center;gap:3px}
.remember span{width:9px;height:9px;border:1px solid #ccc;background:var(--white)}

/* how it works */
.band{left:0;top:670px;width:1200px;height:401px;background:var(--band-bg)}
.how-title{left:186px;top:692px}
.how-text{left:187px;top:726px;width:834px;font-size:10.3px;line-height:18.6px}
.step{top:820px;width:240px;text-align:center}
.step-title{font-family:"Varela Round",sans-serif;font-size:15px;color:var(--green);letter-spacing:.2px}
.step-visual{width:95px;height:95px;margin:14px auto 0;border-radius:10px}
.step-text{margin:11px auto 0;width:228px;font-size:10.3px;line-height:18.6px}

/* footer */
.footer{left:0;top:1071px;width:1200px;height:76px;background:var(--footer-bg)}
.footer-links{left:194px;top:1090px;font-size:10.3px;color:var(--footer-text)}
.footer-copy{left:194px;top:1114px;font-size:10.3px;color:var(--footer-text)}
.social{left:917px;top:1102px;display:flex;gap:8px}
.social span{width:14px;height:14px;border-radius:2px}
</style>
</head>
<body>
<div class="page">

  <header>
    <div class="abs topbar"></div>
    <div class="abs navband"></div>
    <div class="abs brand"><span class="brand-dot"></span>Veldenmoor</div>
    <div class="abs search"><span>Search</span>
      <svg width="10" height="10" viewBox="0 0 10 10"><circle cx="4" cy="4" r="3" fill="none" stroke="#aaa" stroke-width="1.3"/><line x1="6.2" y1="6.2" x2="9.3" y2="9.3" stroke="#aaa" stroke-width="1.5"/></svg>
    </div>
    <nav class="abs main-nav">
      <a href="#">HOME</a><a href="#">ABOUT</a><a href="#">PRODUCTS</a><a href="#">BLOG</a><a href="#">CONTACT</a>
    </nav>
  </header>

  <section>
    <div class="abs hero"></div>
    <div class="abs hero-media" role="img" aria-label="Laptop showing a demo video of facial expression analysis"></div>
    <div class="abs play">
      <svg width="50" height="34" viewBox="0 0 50 34"><polygon points="20,9 20,25 32,17" fill="#111"/></svg>
    </div>
    <h1 class="abs hero-title">Integer bibendum nisl lorem, lobortis male-<br>suada nisl. Curabitur at orci tortor.</h1>
    <p class="abs hero-text">Sed mollis est nec purus egestas et elementum turpis scelerisque. Pellentesque tincidunt ultricies velit, non vehicula orci ullamcorper id. Sed viverra eros eget magna aliquam porttitor. In hac habitasse platea dictumst. Cras eget ullamcorper ligula.</p>
    <a class="abs signup" href="#">SIGNUP NOW
      <span class="signup-arrow"><svg width="10" height="12" viewBox="0 0 10 12"><polygon points="2,1 2,11 9,6" fill="#fff"/></svg></span>
    </a>
    <div class="abs dots"><span></span><span></span><span></span><span></span><span></span></div>
  </section>

  <section>
    <h2 class="abs section-title about-title">About Veldenmoor</h2>
    <p class="abs about-lead">Nulla imperdiet lorem eget neque dictum porta. Vestibulum ante ipsum primis in faucibus orci luctus et ultrices<br>posuere cubilia Curae;</p>
    <p class="abs about-text">Nam aliquam porta mauris, vitae pharetra massa fermentum a. Maecenas lobortis nisl et massa venenatis eu fringilla dolor vehicula. Cras lacinia mollis diam, non feugiat sem venenatis nec. Cras non elit et nulla consequat cursus nec vel magna. Donec ipsum lacus, feugiat sit amet eleifend eget, lacinia vel libero. Nunc ultrices nulla adipiscing magna accumsan congue. Suspendisse est justo, porta ut lacinia at, bibendum non neque. Vestibulum pellentesque velit vel erat elementum in tempor velit luctus. Sed iaculis venenatis quam a commodo. Phasellus ac odio vitae ligula ultricies. Sed ut elit nisi, non mollis sapien. Nunc quis nunc felis. Ut placerat tempor felis id egestas.</p>

    <aside class="abs login">
      <div class="abs login-title">Member Login</div>
      <input class="abs field" style="top:45px" type="text" placeholder="Username">
      <input class="abs field" style="top:78px" type="password" placeholder="Password">
      <div class="abs login-btn">LOGIN</div>
      <div class="abs remember login-small"><span></span>Remeber me</div>
      <div class="abs login-small" style="left:28px;top:163px">Forgot Password?</div>
      <div class="abs login-small" style="left:160px;top:163px">Register Now</div>
    </aside>
  </section>

  <section>
    <div class="abs band"></div>
    <h2 class="abs section-title how-title">How it Works</h2>
    <p class="abs how-text">Etiam mollis tortor at dui commodo eget suscipit quam bibendum. Etiam in odio rhoncus est tincidunt eleifend in et massa. Donec vel orci vehicula tellus pretium condimentum quis in<br>metus. Sed quam velit, accumsan ac gravida non, dignissim quis nisl. Proin tempus laoreet porta. Etiam porta interdum gravida. Sed sed risus non massa egestas dictum. Vestibulum<br>metus mauris, porttitor id congue sed, sollicitudin ac elit.</p>

    <div class="abs step" style="left:194px">
      <div class="step-title">STEP 1 &nbsp;-&nbsp; TITLE GOES HERE</div>
      <div class="step-visual" style="background:linear-gradient(135deg,#e4e8ec,#3fa0f0)" role="img" aria-label="Monitor with satellite dish icon"></div>
      <p class="step-text">Fusce sit amet mi urna, sodales rutrum massa. Aenean eget elit ut ante volutpat tincidunt. Nulla posuere ligula quis est convallis rhoncus. Donec velit mauris, elementum quis dictum et, eleifend a neque.</p>
    </div>
    <div class="abs step" style="left:464px">
      <div class="step-title">STEP 2 &nbsp;-&nbsp; TITLE GOES HERE</div>
      <div class="step-visual" style="background:radial-gradient(circle,#555 0,#1b1b1b 60%)" role="img" aria-label="Webcam icon"></div>
      <p class="step-text">Mauris tincidunt lobortis risus non lobortis. Curabitur ac suscipit lectus. Duis id arcu et ligula fringilla sodales in sit amet nibh. Class aptent taciti sociosqu ad litora torquent per conubia nostra, per inceptos himenaeos.</p>
    </div>
    <div class="abs step" style="left:733px">
      <div class="step-title">STEP 3 &nbsp;-&nbsp; TITLE GOES HERE</div>
      <div class="step-visual" style="background:radial-gradient(circle at 40% 35%,#dbe9f7 0,#7fb6ea 55%,#4a95dc 100%)" role="img" aria-label="Expression results icon"></div>
      <p class="step-text">Praesent faucibus sem vel lacus aliquet luctus. Aliquam non pharetra nisi. Cras dapibus nisl eu lacus porta placerat. Proin porta ultricies velit, vitae dapibus nunc vehicula quis. Cras mattis imperdiet nulla</p>
    </div>
  </section>

  <footer>
    <div class="abs footer"></div>
    <div class="abs footer-links">Home | About | Products | Blog | Contact</div>
    <div class="abs footer-copy">© 2013 Veldenmoor | All Rights Reserved &nbsp;| &nbsp;Privacy policy</div>
    <div class="abs social" aria-label="Social media links">
      <span style="background:#4a6aa8"></span>
      <span style="background:#4fb3e0"></span>
      <span style="background:#2e7ab5"></span>
      <span style="background:#f08a24"></span>
      <span style="background:#d9d9d9"></span>
    </div>
  </footer>

</div>
</body>
</html>
```